Business cards - BRENT Roofing & Siding

We need simple business cards made up for our Roofing & Siding business based in Calgary Alberta.
The logo on one side of the card and potentially our slogan "Built with trust, verified by time".
The other side could have:
-A small logo
-Rep name:
-Rep cell phone:
-Rep email:
-Office phone: 403-684-2093
-Website: PrairieShingleWorks.com

We would like to incorporate the colours from our logo, especially the lite blue on the jpeg file. I have attached the ai file and jpeg file. We like the colours better on the jpeg file.

I do not require a money back guarantee

```html
<!DOCTYPE html>
<html lang="en">
<head>
<meta charset="utf-8">
<title>BRENT Roofing &amp; Siding – Business Cards</title>
<link href="https://fonts.googleapis.com/css2?family=Montserrat:wght@400;500;600&display=swap" rel="stylesheet">
<style>
  :root {
    --backdrop: #3a302c;
    --card: #1e1f21;
    --card-light: #2a2b2d;
    --edge-red: #d0121b;
    --brand-blue: #1f8ff0;
    --text-white: #f2f2f2;
  }
  * { margin: 0; padding: 0; box-sizing: border-box; }
  html, body { width: 1200px; height: 716px; overflow: hidden; }
  body {
    background: var(--backdrop);
    font-family: "Montserrat", sans-serif;
    position: relative;
  }
  .card {
    position: absolute;
    width: 500px;
    height: 286px;
    background: linear-gradient(135deg, var(--card-light), var(--card));
    border-bottom: 4px solid var(--edge-red);
    border-right: 3px solid var(--edge-red);
    box-shadow: 0 14px 30px rgba(0,0,0,.5);
    overflow: hidden;
  }
  .card-front { left: 60px; top: 90px; }
  .card-back { left: 640px; top: 330px; }

  .brand {
    color: var(--text-white);
    font-weight: 600;
    letter-spacing: 2px;
    text-align: center;
    display: flex;
    align-items: center;
    gap: 10px;
    justify-content: center;
  }
  .brand-mark {
    width: 14px; height: 14px;
    background: var(--brand-blue);
    display: inline-block;
  }
  .card-front .brand {
    position: absolute;
    left: 0; right: 0; top: 122px;
    font-size: 28px;
  }
  .card-back .brand {
    position: absolute;
    left: 150px; right: 30px; top: 36px;
    font-size: 17px;
  }

  .divider {
    position: absolute;
    left: 40px; right: 40px; top: 100px;
    height: 1px;
    background: var(--brand-blue);
  }
  .contact-list {
    position: absolute;
    left: 34px; top: 160px;
    list-style: none;
    color: var(--text-white);
    font-size: 13px;
    line-height: 22px;
  }
  .contact-list li { display: flex; align-items: center; gap: 8px; }
  .contact-list svg { width: 11px; height: 11px; flex: none; }

  .rep {
    position: absolute;
    right: 40px; top: 190px;
    text-align: right;
    border-bottom: 1px solid var(--brand-blue);
    padding-bottom: 6px;
  }
  .rep-name {
    color: var(--brand-blue);
    font-weight: 600;
    font-size: 20px;
    text-transform: uppercase;
  }
  .rep-title {
    color: var(--text-white);
    font-size: 13px;
    text-transform: uppercase;
    letter-spacing: 1px;
  }
  .edge-tab {
    position: absolute;
    right: -10px; top: 200px;
    width: 20px; height: 36px;
    border-radius: 10px;
    background: var(--brand-blue);
  }
</style>
</head>
<body>
  <section class="card card-front">
    <div class="brand"><span class="brand-mark"></span>BRENT Roofing &amp; Siding</div>
  </section>

  <section class="card card-back">
    <div class="brand"><span class="brand-mark"></span>BRENT Roofing &amp; Siding</div>
    <div class="divider"></div>
    <ul class="contact-list">
      <li>
        <svg viewBox="0 0 12 12"><path d="M3 1l2 2-1 1.5c.6 1.4 1.6 2.4 3 3L8.5 6.5l2 2L9 10.5C5 10 2 7 1.5 3z" fill="var(--brand-blue)"/></svg>
        403-684-2093
      </li>
      <li>
        <svg viewBox="0 0 12 12"><rect x="3" y="1" width="6" height="10" rx="1" fill="none" stroke="var(--brand-blue)" stroke-width="1.2"/></svg>
        587-310-4478
      </li>
      <li>
        <svg viewBox="0 0 12 12"><rect x="1" y="2.5" width="10" height="7" fill="none" stroke="var(--brand-blue)" stroke-width="1.2"/><path d="M1 3l5 4 5-4" fill="none" stroke="var(--brand-blue)" stroke-width="1.2"/></svg>
        office@brentroofing.ca
      </li>
      <li>
        <svg viewBox="0 0 12 12"><circle cx="6" cy="6" r="5" fill="none" stroke="var(--brand-blue)" stroke-width="1.2"/><path d="M1 6h10M6 1c-2.5 3-2.5 7 0 10M6 1c2.5 3 2.5 7 0 10" fill="none" stroke="var(--brand-blue)" stroke-width="1"/></svg>
        PrairieShingleWorks.com
      </li>
    </ul>
    <div class="rep">
      <div class="rep-name">Dana Whitfield</div>
      <div class="rep-title">Director</div>
    </div>
    <div class="edge-tab"></div>
  </section>
</body>
</html>
```